Fernhollow Brochure - A new residential property investment development in Brisbane Queensland *

I need a brochure to entice and inspire customers of financial planners and alike to buy our investment property development, Fernhollow in Greenbank, Australia.

The brochure will be approximately 16 - 18 pages long and will follow a similar format (including maps etc) to the once attached in the uploaded files, however it is important that it has it's own unique style and brand identify. You will have access to all the renders, maps and autocad drawings that will need to be included in the brochure and will be linked in my dropbox link below.

The brochure should feel sophisticated and use the logo we've previously had developed on studio hive. The background and text should also match the style guidelines of our logo's although happy for you to to get creative with the background as long as it is relevant and fits with the colours. For example stock photo's of tree's, people playing, sunlight etc are great - although the context should be in Australia.

There will be a bit of back and forth once I select the winning designer to ensure the brochure is perfect. I'll also need individual files of the masterplan.

Look forward to seeing your designs.

https://www.filecrate-example.net/sh/q8wz3mfa1tp9rdx/KPLx7vnM2_TTqeZb4Hw9kY1uc?dl=0

Target Market(s)

Financial Planners and their consumer customers

Industry/Entity Type

Real Estate Development

Font styles to use
Other font styles liked:
• Monserrat - as per branding guidelines

Requirements
Must have
• At least all the elements that exist in the example brochures and outlined in the content

dropbox link - https://www.filecrate-example.net/sh/q8wz3mfa1tp9rdx/KPLx7vnM2_TTqeZb4Hw9kY1uc?dl=0

```html
<!DOCTYPE html>
<html lang="en">
<head>
<meta charset="utf-8">
<title>Fernhollow Brochure</title>
<link href="https://fonts.googleapis.com/css2?family=Montserrat:wght@400;500;600;700&display=swap" rel="stylesheet">
<style>
:root{
  --stage:#a8a8ab;
  --paper:#f6f6f6;
  --paper-soft:#eeeeef;
  --blue:#2f6a8f;
  --blue-deep:#24577a;
  --copper:#c4805e;
  --ink:#4a4a4a;
}
*{box-sizing:border-box;margin:0;padding:0}
html,body{width:1200px;height:2180px;overflow:hidden}
body{background:var(--stage);font-family:'Montserrat',sans-serif;color:var(--ink);position:relative}
.page,.spread{position:absolute;background:var(--paper);overflow:hidden;box-shadow:0 6px 14px rgba(0,0,0,.22)}
.fill{position:absolute}
.frame{position:absolute;border:1px solid var(--copper)}
.band{position:absolute;background:var(--copper);color:#fff;font-weight:600;letter-spacing:.5px;padding-left:18px;display:flex;align-items:center;white-space:nowrap}
.brand-word{font-weight:500;color:var(--blue);letter-spacing:1px}

/* cover */
.cover-front{left:70px;top:48px;width:514px;height:369px}
.cover-front .brand-word{position:absolute;left:310px;top:52px;font-size:24px}
.cover-title{position:absolute;left:193px;top:186px;width:194px;height:40px;border:1px solid #fff;color:#fff;text-align:center;font-weight:700;font-size:20px;line-height:38px;letter-spacing:.5px}
.cover-sub{position:absolute;left:193px;top:221px;width:194px;text-align:center;color:#fff;font-size:7px;font-weight:600;letter-spacing:3px;line-height:10px}
.cover-sub span{background:var(--blue);padding:0 5px}
.cover-meta{position:absolute;left:193px;top:244px;width:194px;text-align:center;color:#fff;font-size:10px;font-weight:600;line-height:17px}

.cover-back{left:616px;top:48px;width:514px;height:369px;background:linear-gradient(135deg,#3a7399,var(--blue-deep))}
.cover-back .brand-word{position:absolute;left:0;width:100%;top:52px;text-align:center;color:#fff;font-size:22px}
.back-lead{position:absolute;top:109px;width:100%;text-align:center;color:#fff;font-size:11px}
.back-cta{position:absolute;left:188px;top:129px;width:138px;height:20px;background:var(--copper);color:#fff;font-size:11px;font-weight:700;text-align:center;line-height:20px}
.back-icons{position:absolute;top:157px;width:100%;display:flex;justify-content:center;gap:7px}
.back-contact{position:absolute;top:177px;width:100%;text-align:center;color:#fff;font-size:9px;line-height:17px}
.back-contact strong{font-size:11px}
.partners{position:absolute;left:30px;top:255px;width:454px;height:91px;background:#fff;border:2px solid var(--copper)}
.partners h3{font-size:8px;letter-spacing:2.2px;color:var(--blue);text-align:center;margin-top:10px;font-weight:700}
.partner-row{display:flex;justify-content:space-between;padding:0 10px;margin-top:11px}
.partner-row span{width:30px;height:13px;background:#c9cdd1;border-radius:2px}

/* contents */
.contents{left:68px;top:457px;width:1072px;height:385px}
.contents .side{position:absolute;left:0;top:0;width:306px;height:385px;background:var(--paper-soft)}
.toc{position:absolute;left:56px;top:110px;list-style:none}
.toc li{font-size:10.5px;font-weight:500;height:29.4px;display:flex;align-items:center;gap:16px;color:#333}
.toc li::before{content:"";width:8px;height:8px;border-radius:50%;background:var(--blue)}

/* introduction */
.intro{left:68px;top:882px;width:1072px;height:385px}
.intro-kicker{position:absolute;left:51px;top:101px;font-size:10px;font-weight:600;color:var(--blue);font-variant:small-caps;letter-spacing:.4px}
.intro-body{position:absolute;left:51px;top:136px;width:430px;font-size:10.2px;line-height:14.5px;text-align:justify}
.intro-body p{margin-bottom:14px}
.dropcap{font-size:36px;font-weight:700;color:var(--blue);line-height:24px;float:left;margin-right:2px}

/* amenities */
.amen{left:70px;top:1310px;width:1072px;height:382px}
.amen .spine{position:absolute;left:531px;top:0;width:2px;height:100%;background:rgba(0,0,0,.08)}
.amen-lead{position:absolute;left:51px;top:66px;width:430px;font-size:10px;line-height:14px;text-align:justify}
.amen-lead .brand-word{font-size:18px;letter-spacing:1px;margin-right:3px}
.item{position:absolute;width:370px}
.item .ic{position:absolute;left:-64px;top:0;width:52px;height:52px}
.item h4{font-size:10px;font-weight:600;color:var(--copper);margin-bottom:2px}
.item p{font-size:10px;line-height:14.2px;text-align:justify;margin-bottom:12px}
.amen-mark{position:absolute;left:652px;top:287px;font-size:32px}

/* location */
.loc{left:70px;top:1734px;width:1072px;height:385px}
.map-label{position:absolute;background:var(--copper);color:#fff;font-size:7.5px;font-weight:600;padding:3px 5px;border:1px solid #fff;white-space:nowrap}
.pin{position:absolute;width:22px;height:22px;border-radius:50%;background:var(--blue);border:2px solid #fff}
.loc-panel{position:absolute;left:738px;top:0;width:334px;height:385px;background:var(--paper)}
.stat{position:absolute;display:flex;align-items:flex-end;gap:3px}
.stat b{font-size:40px;font-weight:700;color:var(--copper);line-height:34px}
.stat .u{display:flex;flex-direction:column}
.stat .u span:first-child{background:var(--blue);color:#fff;font-size:10px;font-weight:600;padding:0 5px;letter-spacing:.5px}
.stat .u span:last-child{font-size:8px;font-weight:500;color:#333;margin-top:1px}
</style>
</head>
<body>

<!-- Front cover -->
<section class="page cover-front">
  <svg class="fill" width="514" height="369" viewBox="0 0 514 369" role="img" aria-label="Photograph of a bright bedroom with a made bed, green throw and high windows">
    <defs>
      <linearGradient id="bedWall" x1="0" y1="0" x2="0" y2="1"><stop offset="0" stop-color="#cfcfcd"/><stop offset=".15" stop-color="#9fa8a0"/><stop offset=".3" stop-color="#dcdcda"/><stop offset=".55" stop-color="#c4c2bd"/><stop offset=".72" stop-color="#4f6e4b"/><stop offset=".88" stop-color="#7d7a73"/><stop offset="1" stop-color="#5d5b58"/></linearGradient>
      <radialGradient id="bedGlow" cx=".45" cy=".5" r=".45"><stop offset="0" stop-color="#eae8e3" stop-opacity=".8"/><stop offset="1" stop-color="#eae8e3" stop-opacity="0"/></radialGradient>
      <clipPath id="bedClip"><path d="M0 0 H230 Q160 185 255 369 H0 Z"/></clipPath>
    </defs>
    <g clip-path="url(#bedClip)">
      <rect width="260" height="369" fill="url(#bedWall)"/>
      <rect width="260" height="369" fill="url(#bedGlow)"/>
    </g>
  </svg>
  <span class="brand-word">FERNHOLLOW</span>
  <svg class="fill" width="514" height="369" viewBox="0 0 514 369" aria-hidden="true">
    <circle cx="382" cy="214" r="106" fill="var(--copper)"/>
    <circle cx="289" cy="214" r="112" fill="var(--blue)" opacity=".93"/>
  </svg>
  <div class="cover-title">FERNHOLLOW</div>
  <div class="cover-sub"><span>BROCHURE</span></div>
  <div class="cover-meta">VERSION - 01<br>DATE - 24 / 9 / 2020</div>
</section>

<!-- Back cover -->
<section class="page cover-back">
  <span class="brand-word">FERNHOLLOW</span>
  <p class="back-lead">TO FIND OUT HOW TO SECURE YOUR INVESTMENT IN FERNHOLLOW,</p>
  <div class="back-cta">- CONTACT US NOW -</div>
  <div class="back-icons">
    <svg width="14" height="14" viewBox="0 0 14 14"><circle cx="7" cy="7" r="7" fill="#fff"/><path d="M7 3a2.5 2.5 0 0 0-2.5 2.5C4.5 8 7 11 7 11s2.5-3 2.5-5.5A2.5 2.5 0 0 0 7 3z" fill="var(--blue)"/></svg>
    <svg width="14" height="14" viewBox="0 0 14 14"><circle cx="7" cy="7" r="7" fill="#fff"/><path d="M4 5.5h6l-1 3h-4z" fill="var(--blue)"/><rect x="4" y="4" width="6" height="1.3" rx=".6" fill="var(--blue)"/></svg>
    <svg width="14" height="14" viewBox="0 0 14 14"><circle cx="7" cy="7" r="7" fill="#fff"/><rect x="3.5" y="4.5" width="7" height="5" fill="var(--blue)"/><path d="M3.5 4.5 7 7.5l3.5-3" stroke="#fff" stroke-width=".8" fill="none"/></svg>
  </div>
  <p class="back-contact">27 Tallowwood Lane, Greenbank, QLD 4124<br><strong>1300 555 018</strong><br>sales@fernhollow-example.com.au</p>
  <div class="partners">
    <h3>- WORKING WITH SOME OF AUSTRALIA'S LEADING BRANDS -</h3>
    <div class="partner-row"><span></span><span></span><span></span><span></span><span></span><span></span><span></span><span></span><span></span><span></span><span></span><span></span></div>
    <div class="partner-row"><span></span><span></span><span></span><span></span><span></span><span></span><span></span><span></span><span></span><span></span><span></span></div>
  </div>
</section>

<!-- Contents spread -->
<section class="spread contents">
  <div class="side"></div>
  <svg class="fill" style="left:306px;top:0" width="766" height="385" viewBox="0 0 766 385" role="img" aria-label="Render of an open-plan living and dining room with sliding doors opening onto a fenced garden">
    <defs>
      <linearGradient id="livV" x1="0" y1="0" x2="0" y2="1"><stop offset="0" stop-color="#e2e2e0"/><stop offset=".2" stop-color="#d4d6d3"/><stop offset=".45" stop-color="#bfc3bd"/><stop offset=".72" stop-color="#a8a59e"/><stop offset=".85" stop-color="#77716b"/><stop offset="1" stop-color="#4f4b47"/></linearGradient>
      <radialGradient id="livGarden" cx=".38" cy=".42" rx=".3" ry=".22" r=".3"><stop offset="0" stop-color="#5f7a52"/><stop offset=".55" stop-color="#7b8f6c" stop-opacity=".7"/><stop offset="1" stop-color="#9aa596" stop-opacity="0"/></radialGradient>
      <linearGradient id="livSide" x1="0" y1="0" x2="1" y2="0"><stop offset="0" stop-color="#3d3f3c" stop-opacity=".35"/><stop offset=".08" stop-color="#3d3f3c" stop-opacity="0"/><stop offset=".92" stop-color="#3d3f3c" stop-opacity="0"/><stop offset="1" stop-color="#2f3230" stop-opacity=".45"/></linearGradient>
    </defs>
    <rect width="766" height="385" fill="url(#livV)"/>
    <rect width="766" height="385" fill="url(#livGarden)"/>
    <rect width="766" height="385" fill="url(#livSide)"/>
  </svg>
  <div class="frame" style="left:30px;top:32px;width:473px;height:325px"></div>
  <div class="band" style="left:30px;top:55px;width:243px;height:36px;font-size:24px">CONTENT PAGE</div>
  <ul class="toc">
    <li>ABOUT</li><li>LOCATION PROXIMITY</li><li>SENSE OF COMMUNITY</li><li>INVESTMENT</li>
    <li>POINTS OF INTEREST</li><li>MASTERPLAN</li><li>HOUSE PLANS</li><li>PACKAGE INCLUSIONS</li>
  </ul>
</section>

<!-- Introduction spread -->
<section class="spread intro">
  <svg class="fill" style="left:531px;top:0" width="541" height="385" viewBox="0 0 541 385" role="img" aria-label="Render of a covered outdoor dining patio with wicker chairs and a barbecue bench">
    <defs>
      <linearGradient id="patH" x1="0" y1="0" x2="1" y2="0"><stop offset="0" stop-color="#4e4a47"/><stop offset=".25" stop-color="#6f6b67"/><stop offset=".45" stop-color="#c9cacb"/><stop offset=".75" stop-color="#d8d9d9"/><stop offset="1" stop-color="#bdbebe"/></linearGradient>
      <linearGradient id="patV" x1="0" y1="0" x2="0" y2="1"><stop offset="0" stop-color="#fff" stop-opacity=".1"/><stop offset=".6" stop-color="#cfd0cf" stop-opacity="0"/><stop offset=".78" stop-color="#c6c6c3" stop-opacity=".5"/><stop offset=".93" stop-color="#b0b1ab" stop-opacity=".6"/><stop offset="1" stop-color="#8a9a70"/></linearGradient>
      <radialGradient id="patBench" cx=".78" cy=".6" r=".22"><stop offset="0" stop-color="#4d4e50" stop-opacity=".7"/><stop offset="1" stop-color="#4d4e50" stop-opacity="0"/></radialGradient>
    </defs>
    <rect width="541" height="385" fill="url(#patH)"/>
    <rect width="541" height="385" fill="url(#patV)"/>
    <rect width="541" height="385" fill="url(#patBench)"/>
  </svg>
  <div class="frame" style="left:30px;top:31px;width:473px;height:323px"></div>
  <div class="band" style="left:30px;top:58px;width:243px;height:37px;font-size:24px">INTRODUCTION</div>
  <p class="intro-kicker">An opportunity to invest in long term value creation</p>
  <div class="intro-body">
    <p><span class="dropcap">W</span>elcome to Fernhollow Estate an exclusively (crafted) neighborhood, creating better communities to bring people together.</p>
    <p>Fernhollow has been architecturally designed to create an inviting sense of place, with access to superior home design and generous inclusions as standard. Our exacting approach to our design aesthetic ensures contemporary, comfortable living.</p>
    <p>Nestled between Brisbane and the Gold Coast, Fernhollow is located close to key amenities, services, public transport and major road networks.</p>
    <p>With a limited number of homes available, an investment in Fernhollow provides a unique wealth creation opportunity for the astute investor.</p>
  </div>
</section>

<!-- Amenities spread -->
<section class="spread amen">
  <div class="spine"></div>
  <div class="frame" style="left:30px;top:30px;width:476px;height:323px"></div>
  <div class="frame" style="left:558px;top:30px;width:481px;height:321px"></div>
  <p class="amen-lead"><span class="brand-word">FERNHOLLOW</span> - escape from the hustle and bustle with easy access to established and new amenities - feel like a relaxing glass of wine, picking up that last-minute lotto ticket or jumping on the expresso work, everything is accessible and convenient.</p>

  <div class="item" style="left:115px;top:150px">
    <svg class="ic" viewBox="0 0 52 52"><circle cx="26" cy="26" r="26" fill="var(--blue)"/><path d="M14 30c4-2 8-2 12 0s8 2 12 0M16 23c3-3 7-3 10 0s7 3 10 0" stroke="#fff" stroke-width="3" fill="none" stroke-linecap="round"/></svg>
    <h4>CHILD CARE CENTRES, NEARBY PRIMARY &amp; SECONDARY SCHOOLS.</h4>
    <p>Ridgeview State School and Ridgeview State High school are a 5 minute drive with St Aldric's Catholic Primary School and Greenfield Christian College a short hop. The prestigious Eastmoor Universities, Logan campus is also convenient.</p>
  </div>
  <div class="item" style="left:115px;top:252px">
    <svg class="ic" viewBox="0 0 52 52"><circle cx="26" cy="26" r="26" fill="var(--blue)"/><path d="M17 38V18l8-6 8 6v20M21 38V28h8v10M33 26l6 12" stroke="#fff" stroke-width="2.5" fill="none" stroke-linejoin="round"/></svg>
    <h4>LOCAL PARKS &amp; SPORTING FACILITIES.</h4>
    <p>The Kestrel Bushland Reserve is a fun, safe environment for families to spend quality time –you may even spot an Eastern Grey Kangaroo.</p>
    <p>Fernhollow is also a short drive from soccer and Rugby League fields, Westvale Aquatic Centre and the Stonewater Golf and Country Club.</p>
  </div>

  <div class="item" style="left:638px;top:55px">
    <svg class="ic" viewBox="0 0 52 52"><circle cx="26" cy="26" r="26" fill="var(--blue)"/><path d="M15 30l3-9h16l3 9v7h-3v-3H18v3h-3z" fill="#fff"/><circle cx="20" cy="31" r="1.8" fill="var(--blue)"/><circle cx="32" cy="31" r="1.8" fill="var(--blue)"/><rect x="20" y="23" width="12" height="4" fill="var(--blue)"/></svg>
    <h4>TRANSPORT</h4>
    <p>Ridgeview 'park and ride' is a &lt;time&gt; minute drive with frequent express buses to Brisbane City. In the car Brisbane's CBD is an easy 35-minute drive and the stunning beaches of the Gold Coast can be reached in an hour.</p>
  </div>
  <div class="item" style="left:638px;top:155px">
    <svg class="ic" viewBox="0 0 52 52"><circle cx="26" cy="26" r="26" fill="var(--blue)"/><path d="M13 27 26 15l13 12M17 24v14h18V24" stroke="#fff" stroke-width="3" fill="none" stroke-linejoin="round"/><path d="M26 26v8M22 30h8" stroke="#fff" stroke-width="2.5"/></svg>
    <h4>MEDICAL CLINICS &amp; SPECIALIST SUPPORT SERVICES</h4>
    <p>Hillside Road Medical Centre are only a &lt;time&gt; minute drive away from the estate with more options located in Browns Plains, Logan and Springfield.</p>
  </div>
  <span class="brand-word amen-mark">FERNHOLLOW</span>
</section>

<!-- Location spread -->
<section class="spread loc">
  <svg class="fill" width="738" height="385" viewBox="0 0 738 385" role="img" aria-label="Aerial render of the estate streets and two rows of new white-roofed homes surrounded by bushland">
    <defs>
      <linearGradient id="aerV" x1="0" y1="0" x2="0" y2="1"><stop offset="0" stop-color="#35503a"/><stop offset=".18" stop-color="#4d6248"/><stop offset=".28" stop-color="#c8cbc7"/><stop offset=".4" stop-color="#b7bbb5"/><stop offset=".48" stop-color="#7a6f66"/><stop offset=".56" stop-color="#6e655d"/><stop offset=".64" stop-color="#c4c7c2"/><stop offset=".8" stop-color="#aeb2ab"/><stop offset=".9" stop-color="#4b6146"/><stop offset="1" stop-color="#32492f"/></linearGradient>
      <linearGradient id="aerH" x1="0" y1="0" x2="1" y2="0"><stop offset="0" stop-color="#34503a" stop-opacity=".15"/><stop offset=".75" stop-color="#34503a" stop-opacity="0"/><stop offset=".88" stop-color="#48604a" stop-opacity=".85"/><stop offset="1" stop-color="#3d5840"/></linearGradient>
    </defs>
    <rect width="738" height="385" fill="url(#aerV)"/>
    <rect width="738" height="385" fill="url(#aerH)"/>
  </svg>
  <span class="map-label" style="left:30px;top:98px">RIDGEVIEW TOWN CENTRE- 2.5KM</span>
  <span class="map-label" style="left:228px;top:96px">MERIDIAN PRIVATE HOSPITAL, SPRINGFIELD - 17KM</span>
  <span class="map-label" style="left:130px;top:141px">CENTRAL PLAZA BROWNS PLAINS - 7KM</span>
  <span class="map-label" style="left:355px;top:140px">STONEWATER GOLF COURSE - 20KM</span>
  <span class="pin" style="left:102px;top:198px"></span>
  <span class="pin" style="left:213px;top:198px"></span>
  <span class="pin" style="left:330px;top:198px"></span>
  <span class="pin" style="left:430px;top:198px"></span>

  <div class="loc-panel"></div>
  <div class="frame" style="left:738px;top:30px;width:302px;height:322px;border-left:none"></div>
  <div class="band" style="left:705px;top:56px;width:335px;height:33px;font-size:24px">LOCATION PROXIMITY</div>
  <svg class="fill" style="left:896px;top:89px" width="14" height="285" aria-hidden="true">
    <line x1="7" y1="0" x2="7" y2="272" stroke="var(--copper)" stroke-width="1.2"/>
    <path d="M2 268 7 280 12 268Z" fill="var(--copper)"/>
    <circle cx="7" cy="42" r="4" fill="#fff" stroke="var(--copper)"/>
    <circle cx="7" cy="99" r="4" fill="#fff" stroke="var(--copper)"/>
    <circle cx="7" cy="162" r="4" fill="#fff" stroke="var(--copper)"/>
    <circle cx="7" cy="219" r="4" fill="#fff" stroke="var(--copper)"/>
  </svg>
  <div class="stat" style="left:768px;top:117px"><b>59</b><span class="u"><span>MINUTES</span><span>GOLD COAST</span></span></div>
  <div class="stat" style="left:918px;top:175px"><b>35</b><span class="u"><span>MINUTES</span><span>AIRPORT</span></span></div>
  <div class="stat" style="left:768px;top:240px"><b>30</b><span class="u"><span>MINUTES</span><span>BRISBANE CITY</span></span></div>
  <div class="stat" style="left:918px;top:295px"><b>20</b><span class="u"><span>MINUTES</span><span>LOGAN CITY</span></span></div>
</section>

</body>
</html>
```